Dunmore Roofing

Want a professional looking business card

Industry/Entity Type

Business

Contact Information for Business Card

Paul Dunmore ( Owner) paul@dunmoreroofing-example.com, www.dunmoreroofing-example.com, Adress: 4172 Township road 43 Plantagenet,ON K9X4T2

```html
<!DOCTYPE html>
<html lang="en">
<head>
<meta charset="utf-8">
<title>Dunmore Roofing – Business Card</title>
<link rel="stylesheet" href="https://fonts.googleapis.com/css2?family=Open+Sans:wght@400;600;700&display=swap">
<style>
  :root {
    --stage: #e9e7e3;
    --card-grey: #77787a;
    --card-white: #ffffff;
    --brand-blue: #1d4a8f;
    --text-dark: #2b2b2b;
    --text-muted: #8a8a8a;
    --white: #ffffff;
  }
  * { margin: 0; padding: 0; box-sizing: border-box; }
  html, body {
    width: 1200px;
    height: 635px;
    overflow: hidden;
    background: var(--stage);
    font-family: "Open Sans", Arial, sans-serif;
  }
  .stage {
    position: relative;
    width: 1200px;
    height: 635px;
    display: flex;
    align-items: center;
    justify-content: center;
    gap: 60px;
  }
  .card {
    position: relative;
    width: 520px;
    height: 300px;
    overflow: hidden;
    box-shadow: 0 6px 18px rgba(0,0,0,0.18);
  }

  /* Front */
  .card-front { background: var(--card-grey); }
  .web-pill {
    position: absolute;
    top: 34px;
    right: 0;
    height: 34px;
    padding: 0 26px 0 24px;
    background: var(--brand-blue);
    border-radius: 17px 0 0 17px;
    color: var(--white);
    font-size: 14px;
    line-height: 34px;
    letter-spacing: 0.2px;
  }
  .front-brand {
    position: absolute;
    left: 40px;
    bottom: 44px;
    display: flex;
    align-items: center;
    gap: 12px;
  }
  .brand-mark {
    width: 18px;
    height: 18px;
    background: var(--white);
  }
  .front-brand .brand-name {
    color: var(--white);
    font-size: 30px;
    font-weight: 700;
    text-transform: uppercase;
    letter-spacing: 1.5px;
  }

  /* Back */
  .card-back { background: var(--card-white); }
  .name-tab {
    position: absolute;
    top: 28px;
    left: -18px;
    width: 36px;
    height: 36px;
    border-radius: 50%;
    background: var(--brand-blue);
  }
  .owner {
    position: absolute;
    top: 30px;
    left: 32px;
  }
  .owner-name {
    color: var(--brand-blue);
    font-size: 15px;
    font-weight: 700;
  }
  .owner-role {
    color: var(--text-muted);
    font-size: 12px;
    margin-top: 1px;
  }
  .back-brand {
    position: absolute;
    top: 120px;
    right: 30px;
    color: var(--brand-blue);
    font-size: 22px;
    font-weight: 700;
    text-transform: uppercase;
    letter-spacing: 1px;
    text-align: right;
    line-height: 1.15;
  }
  .contact {
    position: absolute;
    left: 32px;
    bottom: 40px;
    color: var(--text-dark);
    font-size: 12px;
    line-height: 1.4;
  }
  .address { margin-bottom: 10px; }
  .contact-line {
    display: flex;
    align-items: center;
    gap: 8px;
    margin-top: 3px;
  }
  .contact-icon {
    width: 14px;
    height: 14px;
    flex: none;
  }
</style>
</head>
<body>
<main class="stage">

  <section class="card card-front" aria-label="Business card front">
    <div class="web-pill">www.dunmoreroofing-example.com</div>
    <div class="front-brand">
      <span class="brand-mark"></span>
      <span class="brand-name">Dunmore Roofing</span>
    </div>
  </section>

  <section class="card card-back" aria-label="Business card back">
    <span class="name-tab"></span>
    <div class="owner">
      <p class="owner-name">Paul Dunmore</p>
      <p class="owner-role">Owner</p>
    </div>

    <div class="back-brand">Dunmore<br>Roofing</div>

    <div class="contact">
      <p class="address">4172 Township road 43,<br>Plantagenet, ON K9X4T2</p>
      <p class="contact-line">
        <svg class="contact-icon" viewBox="0 0 14 14" aria-hidden="true">
          <rect width="14" height="14" rx="2" fill="#1d4a8f"/>
          <path d="M4.2 3.2l1.4 0 .6 2-1 .8c.5 1.1 1.3 1.9 2.4 2.4l.8-1 2 .6v1.4c0 .5-.4.8-.9.8C6.3 10 4 7.7 3.4 4.1c0-.5.3-.9.8-.9z" fill="#fff"/>
        </svg>
        (613) 555-0142
      </p>
      <p class="contact-line">
        <svg class="contact-icon" viewBox="0 0 14 14" aria-hidden="true">
          <rect width="14" height="14" rx="2" fill="#1d4a8f"/>
          <rect x="3" y="4.2" width="8" height="5.6" fill="none" stroke="#fff" stroke-width="1"/>
          <path d="M3 4.4l4 3 4-3" fill="none" stroke="#fff" stroke-width="1"/>
        </svg>
        paul@dunmoreroofing-example.com
      </p>
      <p class="contact-line">
        <svg class="contact-icon" viewBox="0 0 14 14" aria-hidden="true">
          <rect width="14" height="14" rx="2" fill="#1d4a8f"/>
          <circle cx="7" cy="7" r="3.6" fill="none" stroke="#fff" stroke-width="1"/>
          <path d="M3.4 7h7.2M7 3.4c-1.6 2-1.6 5.2 0 7.2M7 3.4c1.6 2 1.6 5.2 0 7.2" fill="none" stroke="#fff" stroke-width="0.8"/>
        </svg>
        www.dunmoreroofing-example.com
      </p>
    </div>
  </section>

</main>
</body>
</html>
```